Web Developer Needs a Business Card Design

I need a personal business card design that represents me as a web developer for potential employers. I would like the background to be a dark color on the front for contrast with my logo and name. The back will have all my information along with a smaller version of the logo. I want something with a modern look and feel, not too conservative. This will be used for potential employers and freelance work.

Industry/Entity Type

Business

Contact Information for Business Card

Front should have my logo and name. The back should have all my personal information which would include: name: Tom Varulek, phone: 570-614-3098, email: tomvarulek@quillbox.net, website url: www.tomvarulek.net, logo, web developer.

Font styles to use
Sans Serif

Requirements
Must have
• Must include my logo. The color palette base color will be the logo color.

```html
<!DOCTYPE html>
<html lang="en">
<head>
<meta charset="utf-8">
<title>Tom Varulek — Business Card</title>
<link rel="stylesheet" href="https://fonts.googleapis.com/css2?family=Roboto:wght@300;400&family=Source+Sans+3:wght@400;600&display=swap">
<style>
  :root {
    --teal: #47c6a7;
    --page: #8a8b8b;
    --card-dark: #2a2322;
    --card-light: #ebebeb;
    --ink: #4a4a4a;
    --muted: #6b6b6b;
    --rule: #b9b9b9;
    --on-dark: #e9e9e9;
  }
  * { margin: 0; padding: 0; box-sizing: border-box; }
  html, body { width: 1200px; height: 900px; overflow: hidden; }
  body { background: var(--page); position: relative; font-family: "Source Sans 3", sans-serif; }

  .card { position: absolute; left: 330px; width: 540px; height: 308px; overflow: hidden; }

  /* Front */
  .card--front { top: 110px; }
  .front-photo {
    position: absolute; inset: 0;
    background: radial-gradient(ellipse at 50% 85%, #121010 0%, #2c2423 45%, #2f2a29 100%);
  }
  .front-mark {
    position: absolute; left: 219px; top: 52px; width: 102px; height: 102px;
    border: 6px solid var(--teal); border-radius: 50%;
  }
  .front-name {
    position: absolute; top: 182px; width: 100%; text-align: center;
    font-family: "Roboto", sans-serif; font-weight: 300; font-size: 29px;
    letter-spacing: 1.5px; color: var(--on-dark);
  }
  .front-role {
    position: absolute; top: 230px; width: 100%; text-align: center;
    font-family: "Roboto", sans-serif; font-weight: 300; font-size: 15px;
    letter-spacing: 1px; color: #cfcfcf;
  }

  /* Back */
  .card--back { top: 478px; background: var(--card-light); }
  .back-mark {
    position: absolute; left: 98px; top: 72px; width: 146px; height: 146px;
    border: 5px solid var(--teal); border-radius: 50%;
    display: flex; align-items: center; justify-content: center;
  }
  .back-mark__name { color: var(--teal); font-weight: 600; font-size: 19px; }
  .back-divider {
    position: absolute; left: 270px; top: 60px; width: 1px; height: 176px; background: var(--rule);
  }
  .back-info { position: absolute; left: 297px; top: 52px; }
  .back-name { color: var(--teal); font-weight: 600; font-size: 20px; line-height: 24px; }
  .back-role { color: var(--muted); font-size: 15px; line-height: 20px; margin-bottom: 14px; }
  .contact { list-style: none; }
  .contact li {
    display: flex; align-items: center; gap: 8px;
    font-size: 13.5px; line-height: 20.6px; color: var(--ink);
  }
  .contact svg { width: 14px; height: 14px; flex: none; }
  .contact .dot { width: 12px; height: 12px; margin: 0 1px; border-radius: 50%; background: var(--teal); flex: none; }
  .back-band-line { position: absolute; left: 0; right: 0; bottom: 22px; height: 2px; background: #cfcfcf; }
  .back-band { position: absolute; left: 0; right: 0; bottom: 0; height: 22px; background: var(--teal); }
</style>
</head>
<body>

  <section class="card card--front">
    <div class="front-photo" role="img" aria-label="Dark top-down photo of a desk with a laptop, keyboard and a cup of coffee"></div>
    <div class="front-mark"></div>
    <h1 class="front-name">TOM VARULEK</h1>
    <p class="front-role">Front-End Developer</p>
  </section>

  <section class="card card--back">
    <div class="back-mark"><span class="back-mark__name">Tom Varulek</span></div>
    <div class="back-divider"></div>
    <div class="back-info">
      <h2 class="back-name">Tom Varulek</h2>
      <p class="back-role">Front-End Developer</p>
      <ul class="contact">
        <li>
          <svg viewBox="0 0 24 24"><path fill="var(--teal)" d="M6.6 10.8a15 15 0 0 0 6.6 6.6l2.2-2.2a1 1 0 0 1 1-.25 11.4 11.4 0 0 0 3.6.57 1 1 0 0 1 1 1V20a1 1 0 0 1-1 1A17 17 0 0 1 3 4a1 1 0 0 1 1-1h3.5a1 1 0 0 1 1 1c0 1.25.2 2.45.57 3.6a1 1 0 0 1-.25 1z"/></svg>
          570-614-3098
        </li>
        <li>
          <svg viewBox="0 0 24 24"><rect x="2" y="5" width="20" height="14" rx="1" fill="var(--teal)"/><path d="M3 6l9 7 9-7" fill="none" stroke="#ebebeb" stroke-width="1.8"/></svg>
          tomvarulek@quillbox.net
        </li>
        <li>
          <svg viewBox="0 0 24 24"><circle cx="12" cy="12" r="10" fill="var(--teal)"/><path d="M2 12h20M12 2c3 3 3 17 0 20M12 2c-3 3-3 17 0 20" fill="none" stroke="#ebebeb" stroke-width="1.5"/></svg>
          www.tomvarulek.net
        </li>
        <li><span class="dot"></span>@tomvarulek.net</li>
        <li><span class="dot"></span>tomvarulek.net</li>
        <li><span class="dot"></span>tomvarulek.net</li>
      </ul>
    </div>
    <div class="back-band-line"></div>
    <div class="back-band"></div>
  </section>

</body>
</html>
```